Awesome photographers card for an awesome new business

Double sided business card Black background and silver logo in middle on one side. Details on otherside. please keep it simple

Industry/Entity Type

Photographer

Contact Information for Business Card

Gerald Fenwick
0452817360
GeraldFenwickPhotography47@mailbox.test
www.GeraldFenwickPhotography.test.au
Instagram _Gerald_fenwick

Requirements
Must have
• My logo in Silver
• please use instagram logo instead of "Instagram"

```html
<!DOCTYPE html>
<html lang="en">
<head>
<meta charset="utf-8">
<title>Gerald Fenwick Photography – Business Card</title>
<link href="https://fonts.googleapis.com/css2?family=Lato:wght@400;700&display=swap" rel="stylesheet">
<style>
  :root {
    --backdrop: #3a322d;
    --card: #23292c;
    --silver: #dcdcdc;
    --silver-soft: #c9c9c9;
  }
  * { box-sizing: border-box; margin: 0; padding: 0; }
  html, body {
    width: 1200px; height: 780px; overflow: hidden;
    background: var(--backdrop);
    font-family: 'Lato', sans-serif;
  }
  .canvas {
    width: 1200px; height: 780px;
    display: flex; align-items: center; justify-content: center; gap: 50px;
  }
  .card {
    width: 520px; height: 300px;
    background: var(--card);
    border-radius: 3px;
    box-shadow: 0 14px 30px rgba(0,0,0,.45);
    position: relative;
    overflow: hidden;
    color: var(--silver);
  }

  /* Front: centred logo */
  .card--front { display: flex; align-items: center; justify-content: center; }
  .brand {
    width: 170px; height: 170px;
    border-radius: 50%;
    border: 3px solid var(--silver);
    display: flex; align-items: center; justify-content: center;
    text-align: center;
  }
  .brand__name {
    font-size: 22px; font-weight: 400; letter-spacing: 1px;
    line-height: 1.25; color: var(--silver);
  }

  /* Back: details */
  .card__ring {
    position: absolute; left: -60px; top: -90px;
    width: 300px; height: 300px; border-radius: 50%;
    border: 3px solid var(--silver);
  }
  .details {
    position: absolute; left: 228px; top: 138px; right: 16px;
  }
  .details__name {
    font-size: 17px; font-weight: 700; letter-spacing: .5px;
    text-transform: uppercase; color: var(--silver); margin-bottom: 12px;
  }
  .contact-list { list-style: none; }
  .contact-list li {
    display: flex; align-items: center; gap: 7px;
    font-size: 13px; color: var(--silver-soft); line-height: 19px;
  }
  .contact-list .icon { width: 13px; height: 13px; flex: none; }
  .details__web {
    font-size: 13px; color: var(--silver-soft); margin-top: 3px; margin-left: -14px;
  }
</style>
</head>
<body>
<main class="canvas">

  <section class="card card--front" aria-label="Card front">
    <div class="brand">
      <span class="brand__name">Gerald<br>Fenwick</span>
    </div>
  </section>

  <section class="card card--back" aria-label="Card back">
    <div class="card__ring" aria-hidden="true"></div>
    <div class="details">
      <h1 class="details__name">Gerald Fenwick</h1>
      <ul class="contact-list">
        <li>
          <svg class="icon" viewBox="0 0 16 16" aria-hidden="true">
            <circle cx="8" cy="8" r="7.2" fill="none" stroke="#c9c9c9" stroke-width="1.2"/>
            <path d="M5.6 4.4l1.3 1.4-.7 1a5 5 0 0 0 2.9 2.9l1-.7 1.4 1.3-.8 1.2c-2.9-.3-5.3-2.7-5.6-5.6z" fill="#c9c9c9"/>
          </svg>
          <span>0452817360</span>
        </li>
        <li>
          <svg class="icon" viewBox="0 0 16 16" aria-hidden="true">
            <circle cx="8" cy="8" r="7.2" fill="none" stroke="#c9c9c9" stroke-width="1.2"/>
            <rect x="4" y="5.2" width="8" height="5.6" fill="#c9c9c9"/>
            <path d="M4 5.4l4 3 4-3" fill="none" stroke="#23292c" stroke-width="0.9"/>
          </svg>
          <span>GeraldFenwickPhotography47@mailbox.test</span>
        </li>
        <li>
          <svg class="icon" viewBox="0 0 16 16" aria-hidden="true">
            <circle cx="8" cy="8" r="7.2" fill="none" stroke="#c9c9c9" stroke-width="1.2"/>
          </svg>
          <span>_Gerald_fenwick</span>
        </li>
      </ul>
      <p class="details__web">www.GeraldFenwickPhotography.test.au</p>
    </div>
  </section>

</main>
</body>
</html>
```